Personal Blog

The wordpress blog style and layout should be similar to http://www.samfenwick.com

homepage: my photo, list of things, call to action then 3 boxes (The Blog, The Book and podcast)

Other pages: About us, Blog, Consulting, Contact

Target Market(s)

Web Marketing Consultant

Industry/Entity Type

Consulting

Colors
3277b5
33a6d7
f04a50
f68e4e
33b7a4

```html
<!DOCTYPE html>
<html lang="en">
<head>
<meta charset="utf-8">
<title>Karim Nasser — Consulting</title>
<link href="https://fonts.googleapis.com/css2?family=Oswald:wght@400;500&family=Open+Sans:wght@400;600;700&display=swap" rel="stylesheet">
<style>
:root{
  --navy:#1c2533;
  --navy-2:#141b26;
  --orange:#f68e4e;
  --orange-dark:#e9763a;
  --blue:#3277b5;
  --sky:#33a6d7;
  --teal:#33b7a4;
  --red:#f04a50;
  --page:#e7e8ea;
  --white:#ffffff;
  --text:#3a3d42;
  --muted:#7b8088;
  --line:#d9dbde;
  --row:#f3f3f3;
}
*{box-sizing:border-box;margin:0;padding:0}
html,body{width:1200px;height:3686px;overflow:hidden}
body{background:var(--page);font-family:"Open Sans",Arial,sans-serif;color:var(--text);font-size:15px;line-height:1.55;position:relative}
.abs{position:absolute}
h1,h2,h3,h4,.nav a,.btn{font-family:"Oswald",Arial,sans-serif;font-weight:400}

/* header */
.site-header{left:0;top:0;width:1200px;height:155px;background:var(--navy)}
.brand{left:70px;top:48px;display:flex;align-items:center;gap:14px;color:var(--white);font-family:"Oswald",sans-serif;font-size:40px;line-height:1}
.brand-mark{width:40px;height:40px;background:var(--orange)}
.nav{right:50px;top:58px;display:flex;gap:34px}
.nav a{color:var(--white);text-decoration:none;font-size:19px;letter-spacing:.5px;text-transform:uppercase;padding-bottom:6px}
.nav a.active{color:var(--orange);border-bottom:3px solid var(--orange)}

/* main column */
.main{left:53px;top:190px;width:720px;height:3068px;background:var(--white);padding:40px 32px}
.page-title{font-size:30px;color:var(--text);text-transform:uppercase;margin-bottom:12px}
.main p{margin-bottom:16px}
.video{width:524px;height:280px;border:6px solid var(--sky);background:linear-gradient(135deg,#dfe7ef,#b9c8d8 60%,#8fa3b8);position:relative;margin:150px 0 16px}
.video-tag{left:-6px;top:100px;background:var(--orange);color:var(--white);font-family:"Oswald",sans-serif;font-size:22px;padding:8px 22px}
.play{left:222px;top:100px}
.narrow{width:530px}
.section-title{font-size:17px;font-weight:700;font-family:"Open Sans",sans-serif;margin:40px 0 18px}
.service{display:flex;gap:18px;background:var(--row);border-right:4px solid var(--orange);height:92px;margin-bottom:11px;align-items:center}
.service-thumb{width:94px;height:92px;background:linear-gradient(135deg,#c9d3dc,#8a9bad)}
.service h4{font-family:"Open Sans",sans-serif;font-weight:600;color:var(--orange);font-size:15px;margin-bottom:2px}
.service p{font-size:13px;line-height:1.45;margin:0}
.story{list-style:none}
.story li{position:relative;padding-left:24px;font-size:13px;line-height:1.5;margin-bottom:14px}
.story li::before{content:"";position:absolute;left:2px;top:6px;border-left:8px solid var(--orange);border-top:5px solid transparent;border-bottom:5px solid transparent}
.story strong{display:block;font-size:14px}
.field{border:2px solid var(--line);border-radius:4px;height:50px;padding:12px 16px;color:var(--muted);font-size:14px}
.btn{display:inline-block;background:var(--orange);color:var(--white);text-transform:uppercase;text-align:center;font-size:22px;border-radius:3px}
.pager{display:flex;align-items:center;gap:10px;font-size:13px;color:var(--muted)}
.pager span{border:1px solid var(--line);padding:5px 11px;border-radius:3px}

/* sidebar */
.about{left:800px;top:190px;width:360px;height:470px;background:var(--white);text-align:center;padding:22px 30px}
.portrait{width:196px;height:196px;border-radius:50%;margin:0 auto 30px;background:linear-gradient(160deg,#d8e1ea,#8fa0b4)}
.about h3{font-size:24px;margin-bottom:8px}
.about p{font-size:13px;line-height:1.5;color:var(--muted)}
.about a{color:var(--orange);font-weight:600;text-decoration:none}
.optin{left:800px;top:820px;width:360px;height:530px;background:var(--navy);color:var(--white);padding:38px 36px}
.optin h3{font-size:27px;line-height:1.2;text-transform:uppercase;margin-bottom:14px}
.optin p{font-size:14px;line-height:1.5;margin-bottom:22px}
.optin .field{background:var(--white);border:none;height:48px;margin-bottom:24px}
.banner{left:800px;width:360px}
.search{left:800px;top:2905px;width:360px}

/* footer */
.site-footer{left:0;top:3410px;width:1200px;height:276px;background:var(--navy);color:var(--white)}
.site-footer h3{font-size:27px;text-transform:uppercase;margin-bottom:12px}
.site-footer p{font-size:13px;line-height:1.5}
.site-footer .field{background:var(--white);border:none;height:38px;padding:8px 12px;margin-bottom:10px;font-size:13px}
.social{display:flex;gap:14px}
.social i{display:block;width:56px;height:56px;background:#3a4556;border-radius:4px}
.copyright{left:0;top:3640px;width:1200px;height:46px;background:var(--navy-2);text-align:center;font-size:13px;line-height:46px}
.copyright b{color:var(--orange);font-weight:400}
</style>
</head>
<body>

<header class="site-header abs">
  <div class="brand abs"><span class="brand-mark"></span>Karim Nasser</div>
  <nav class="nav abs">
    <a href="#">About</a><a href="#">Blog</a><a href="#" class="active">Consulting</a><a href="#">Resources</a><a href="#">Book</a><a href="#">Contact</a>
  </nav>
</header>

<main class="main abs">
  <h1 class="page-title">Consulting Services</h1>
  <p>Our consulting services putting the customer at the heart of the business is something that most organisations have been thinking and talking about for years.</p>
  <p>We will help you understand who your customers really are so you can unlock the long-term value and growth potential of your business. By understanding what your customers want and like, and how they really behave, you can sell more of what they do want and avoid wasting money on providing what they don't.</p>

  <div class="video" role="img" aria-label="Video still of a consultant sketching a marketing plan on a whiteboard">
    <div class="video-tag abs">How it work?</div>
    <svg class="play abs" width="80" height="80" viewBox="0 0 80 80"><circle cx="40" cy="40" r="38" fill="#f68e4e"/><path d="M31 23 L59 40 L31 57 Z" fill="#fff"/></svg>
  </div>
  <p class="narrow">Well-searched marketing services drive up both revenue and profits. We works with companies to structure such programs carefully to target attractive customer segments, create the desired image and strengthen the brand.</p>
  <p style="margin-top:80px">Our offer is simple and compelling - we can improve customer satisfaction and increase your revenue.</p>

  <h2 class="section-title">What we do</h2>
  <div class="service"><div class="service-thumb" role="img" aria-label="Product management photo"></div><div><h4>Product Management</h4><p>Lorem ipsum dolor sit amet, consectetur adipiscing elit, sed do eiusmod<br>tempor incididunt ut labore et dolore magna aliqua. enim ad minim</p></div></div>
  <div class="service"><div class="service-thumb" role="img" aria-label="Customer development photo"></div><div><h4>Customer Development</h4><p>Lorem ipsum dolor sit amet, consectetur adipiscing elit, sed do eiusmod<br>tempor incididunt ut labore et dolore magna aliqua. enim ad minim</p></div></div>
  <div class="service"><div class="service-thumb" role="img" aria-label="Digital marketing photo"></div><div><h4>Digital Marketing</h4><p>Lorem ipsum dolor sit amet, consectetur adipiscing elit, sed do eiusmod<br>tempor incididunt ut labore et dolore magna aliqua. enim ad minim</p></div></div>
  <div class="service"><div class="service-thumb" role="img" aria-label="Branding and reputation photo"></div><div><h4>Branding &amp; Reputation</h4><p>Lorem ipsum dolor sit amet, consectetur adipiscing elit, sed do eiusmod<br>tempor incididunt ut labore et dolore magna aliqua. enim ad minim</p></div></div>
  <div class="service"><div class="service-thumb" role="img" aria-label="Entrepreneurship photo"></div><div><h4>Entrepreneurship</h4><p>Lorem ipsum dolor sit amet, consectetur adipiscing elit, sed do eiusmod<br>tempor incididunt ut labore et dolore magna aliqua. enim ad minim</p></div></div>

  <h2 class="section-title">Client Result Story</h2>
  <ul class="story">
    <li><strong>Lorem ipsum dolor sit amet, consectetur adipiscing elit</strong>Lorem ipsum dolor sit amet, consectetur adipiscing elit, sed do eiusmod tempor incididunt ut labore et dolore magna aliqua. Ut enim ad minim veniam, quis nostrud exercitation ullamco laboris nisi ut aliquip ex ea commodo.</li>
    <li><strong>Lorem ipsum dolor sit amet, consectetur adipiscing elit</strong>Lorem ipsum dolor sit amet, consectetur adipiscing elit, sed do eiusmod tempor incididunt ut labore et dolore magna aliqua. Ut enim ad minim veniam, quis nostrud exercitation ullamco laboris nisi ut aliquip ex ea commodo.</li>
    <li><strong>Lorem ipsum dolor sit amet, consectetur adipiscing elit</strong>Lorem ipsum dolor sit amet, consectetur adipiscing elit, sed do eiusmod tempor incididunt ut labore et dolore magna aliqua. Ut enim ad minim veniam, quis nostrud exercitation ullamco laboris nisi ut aliquip ex ea commodo.</li>
    <li><strong>Lorem ipsum dolor sit amet, consectetur adipiscing elit</strong>Lorem ipsum dolor sit amet, consectetur adipiscing elit, sed do eiusmod tempor incididunt ut labore et dolore magna aliqua. Ut enim ad minim veniam, quis nostrud exercitation ullamco laboris nisi ut aliquip ex ea commodo.</li>
    <li><strong>Lorem ipsum dolor sit amet, consectetur adipiscing elit</strong>Lorem ipsum dolor sit amet, consectetur adipiscing elit, sed do eiusmod tempor incididunt ut labore et dolore magna aliqua. Ut enim ad minim veniam, quis nostrud exercitation ullamco laboris nisi ut aliquip ex ea commodo.</li>
  </ul>

  <h2 class="section-title" style="margin-top:70px">How can we help you?</h2>
  <p style="font-size:14px">Leave the message to discuss how our team can help your business achieve true results.</p>
  <div style="display:flex;gap:28px;margin-top:100px">
    <div class="field" style="width:330px">Name</div>
    <div class="field" style="width:330px">Email</div>
  </div>
  <div class="field" style="height:245px;margin-top:30px">Email</div>
  <span class="btn" style="width:110px;height:50px;line-height:50px;margin-top:34px">Send</span>

  <div class="pager" style="margin-top:175px">
    <span>Previous</span><span>1</span><span>2</span><span>3</span><span>4</span><span>5</span><span>...</span><span>30</span>
    <span class="btn" style="margin-left:auto;font-size:15px;padding:4px 30px;border:none">Next</span>
  </div>
</main>

<aside>
  <section class="about abs">
    <div class="portrait" role="img" aria-label="Portrait photo of Karim Nasser"></div>
    <h3>ABOUT ME</h3>
    <p>Lorem ipsum dolor sit amet, con sectetur adipiscing elit, sed do eiusmod tempor incididunt ut labore et dolore magna aliqua. Ut enim ad minim veniam, quis nos trud citation ullamco laboris nisi ut aliquip ex ea commodo nisi ut aliquip ex ea commodo. Lorem ipsum dolor sit amet, sed with me <a href="#">Click here</a></p>
  </section>

  <section class="optin abs">
    <h3>Join my new business bootcamp for free</h3>
    <p>Learn how to create raving fans with free eBooks, get started with online video and podcasting, engage with social media and blog your way to business success, plus much more!</p>
    <div class="field">Enter your name...</div>
    <div class="field">Enter your email...</div>
    <span class="btn" style="width:100%;height:48px;line-height:48px">Join for free!</span>
  </section>

  <div class="banner abs" style="top:1393px;height:342px;background:linear-gradient(160deg,#33a6d7,#33b7a4 55%,#2b6f91)" role="img" aria-label="Event banner with a beach scene and speaker photos"></div>
  <div class="banner abs" style="top:1775px;height:345px;background:linear-gradient(160deg,#f5f5f2,#cfe3ea 60%,#8fc0d2)" role="img" aria-label="Remote Growth Circle banner with a laptop on a beach"></div>
  <div class="banner abs" style="top:2160px;height:350px;background:linear-gradient(160deg,#d7f0ec,#33b7a4 70%,#1f8c7d)" role="img" aria-label="Team Finder Desk banner with an illustrated assistant"></div>
  <div class="banner abs" style="top:2548px;height:332px;background:linear-gradient(180deg,#ffffff,#e7e2da 70%,#1c2533 88%)" role="img" aria-label="Brand Builder Camp banner with paper boats"></div>

  <div class="search abs">
    <div class="field" style="height:44px;padding:10px 14px;font-size:13px;background:#fff">Search Archive...</div>
    <span class="btn" style="width:130px;height:46px;line-height:46px;margin-top:20px;font-size:20px">Search</span>
  </div>
</aside>

<footer class="site-footer abs">
  <div class="abs" style="left:48px;top:30px;width:330px">
    <h3>Entrepreneur, Speaker,</h3>
    <p>Lorem Ipsum is simply dummy text of the printing &amp; typesetting industry. Lorem Ipsum has been industry's standard dummy text ever since the 1500s.</p>
    <p style="margin-top:10px">Lorem Ipsum is simply dummy text of the printing &amp; typesetting industry.</p>
    <p style="color:var(--orange)">[ Read the long-winded version! ]</p>
  </div>
  <div class="abs" style="left:422px;top:30px;width:340px">
    <h3>Join my new business</h3>
    <div class="field">Enter your name...</div>
    <div class="field">Enter your email...</div>
    <span class="btn" style="width:100%;height:44px;line-height:44px">Join for free!</span>
  </div>
  <div class="abs" style="left:800px;top:30px;width:340px">
    <h3>Connect with me</h3>
    <div class="social"><i></i><i></i><i></i><i></i></div>
    <p style="margin:16px 0 0 40px">OR</p>
    <p>Connect with via <span style="color:var(--orange)">email</span></p>
  </div>
</footer>
<div class="copyright abs" style="color:#fff">© 2014 K. Nasser <b>www.karimnasser.com</b> | All Right Reserved.</div>

</body>
</html>
```